Small Business Directory Site Requires a Professional Responsive Web Design

Small Business Directory and Coupon Site - we require a complete website design for a brand new responsive & mobile friendly website. We already have a coder who will professional code our website in Magento.

All PSD pages need to be professionally designed then uploaded into a sharedrive (i.e. like filecrate). Additionally, as I cannot pre-empt everything, please note that we may require a little more assistance once the files have been transferred (for example, in www.brightlane-listings.example if you hover your mouse on the search box you will see a pop up box. We want one of these too and I think that means there may be extra design work here)

We have some draft page sketches have been created (there are some minor changes we want to the sketches provided though); however, we require an excellent designer to add the creative touches to it to make it look professionally created. All artwork/font must be legal.

-------------------------
We like the look of the www.brightlane-listings.example and www. marlowfolio.example

For the headers, please consider a font similar to RNS camellia. We likes this style, but it is too thin for the headers...so we need a variation like this one. For the copy/general text font, something basic that marries well with the headers.

---------------------

Please be sure to also read the brief we wrote for the coder as this will help with better understanding our design requirements.

In total I believe we have about 50 pages. This includes all the little pages and most of the pop up boxes (but not the little help key boxes). For example, pages include...

1. Login (this is where customers log in and can edit, manage their profiles. This means that there are backend membership pages)
2. Mini Services (same look and feel as the business coupons)
3. Resource Centre
4. Join (this is where customers learn about the packages available to submit a directory listing, if they ‘buy’ a package (i.e. free, $25 or $150 package) then they can create their own directory listing)
5. Search the directory (customer can view all the categories and also search the directory)
6. Create a directory listing (this is where customers learn about the packages available to submit a directory listing, if they ‘buy’ a package (i.e. free, $25 or $150 package) then they can create their own directory listing)
7. Quote finder (also know as Get a Quote)
8. Coupons (customer go to the business coupon page and can view all current coupons/submit a coupon)
9. Submit a coupon (form)
10.Advertise with us (form)
11. Join the forum
12.Submit an article or video (form)
13. Affiliates (listing of affiliates we currently have)
14. Become an affiliate (form)
15. Case studies (customer can view the case studies we have in the resource centre)
16. Help Guides (customer can view the help guides we have in the resource centre)
17. About Us
18 .Contact Us (form)
19. Terms & Condition
20. Privacy Policy
21. Supporting City Councils
22. Site Map
23. Forgot password / login details
24. Homepage
25. If we hover over a few areas (i.e. search box, location field) it pops up with more information.
etc etc etc. . . there are more pages.

Please see our filecrate link for the draft mock up pages that I have created so far.

https://www.cloudtrunk.example/sh/qk72pmw4rtz8nd/KLMvbTq2fWndxPzs8Yh4ecRQu

We are in a rush! We'd like to get the majority of the artwork completed by the end of the month. Minor fixes/tweaks can occur thereafter.

Target Market(s)

Small Businesses (employees 0 - 50) located throughout Australia

Industry/Entity Type

Business

Font styles to use
Sans Serif

Requirements
Must have
• Professional. Artwork must be legal (cannot be cut and paste or taken off other websites, must be legally purchased and used).Must look contemporary, fresh, modern.

Absolutely must be a responsive site!
Nice to have
• original work, original photos, original art.

like modern, fresh photos that demonstrate innovation, growth, small business, Australian scenery, stability, goals/passion.
Should not have
• cut and paste graphics, illegal graphics, not purchased graphics.

```html
<!DOCTYPE html>
<html lang="en">
<head>
<meta charset="utf-8">
<title>Smallbiz Anchor – Australia's Small Business Directory</title>
<link rel="stylesheet" href="https://fonts.googleapis.com/css2?family=Open+Sans:wght@400;600;700&family=Raleway:wght@400;600;700;800&display=swap">
<style>
:root{
  --orange:#f26a21;
  --orange-dark:#d9561a;
  --ink:#333333;
  --muted:#777777;
  --line:#dddddd;
  --white:#ffffff;
  --night:#151515;
  --night-2:#222222;
  --footer:#1c1c1c;
  --footer-bar:#111111;
  --paper:#eef0f2;
}
*{box-sizing:border-box;margin:0;padding:0}
html,body{width:1200px;height:2184px;overflow:hidden}
body{position:relative;background:var(--white);font-family:"Open Sans",Arial,sans-serif;color:var(--ink);font-size:13px}
.abs{position:absolute}
h1,h2,h3,h4{font-family:"Raleway","Open Sans",sans-serif}

/* header */
.site-header{position:absolute;left:0;top:0;width:1200px;height:104px;background:var(--white);border-bottom:1px solid var(--line)}
.brand{position:absolute;left:110px;top:22px;display:flex;align-items:center;gap:10px}
.brand-square{width:30px;height:30px;background:var(--orange)}
.brand-name{font-family:"Raleway",sans-serif;font-weight:700;font-size:22px;color:var(--ink);letter-spacing:.5px}
.social-top{position:absolute;left:826px;top:12px;display:flex;gap:8px}
.social-top span{width:16px;height:16px;border-radius:50%;background:#9a9a9a}
.login-bar{position:absolute;left:912px;top:10px;display:flex;gap:6px}
.login-bar .field{width:88px;height:22px;border:1px solid var(--line);font-size:11px;color:var(--muted);padding:3px 7px}
.login-bar .btn{height:22px;padding:3px 14px;background:var(--orange);color:var(--white);font-size:11px;font-weight:600}
.main-nav{position:absolute;left:470px;top:66px;display:flex}
.main-nav a{display:block;padding:8px 20px;font-size:13px;color:var(--muted);text-decoration:none;border-left:1px solid var(--line)}
.main-nav a:first-child{border-left:none}
.main-nav a.current{color:var(--orange);font-weight:600;border-bottom:3px solid var(--orange)}

/* hero */
.hero{position:absolute;left:0;top:104px;width:1200px;height:496px;
  background:linear-gradient(160deg,#e9e3d6 0%,#b9ad92 30%,#7d6a4c 60%,#4a3a28 85%,#3a2c1d 100%)}
.hero-title{position:absolute;left:120px;top:224px;font-family:"Raleway",sans-serif;font-weight:800;color:var(--night-2);line-height:1.1}
.hero-title .l1{font-size:30px}
.hero-title .l2{font-size:30px}
.hero-title em{font-style:normal;color:var(--orange)}
.hero-search{position:absolute;left:120px;top:318px;display:flex;gap:6px}
.hero-search .field{height:34px;background:var(--white);border:1px solid #ccc;font-size:12px;color:var(--muted);padding:8px 10px}
.hero-search .what{width:300px}
.hero-search .where{width:190px}
.hero-search .go{width:58px;height:34px;background:var(--orange);color:var(--white);font-weight:700;font-size:15px;text-align:center;line-height:34px}
.listing-panel{position:absolute;left:888px;top:168px;width:300px;height:330px;background:var(--orange);padding:16px}
.listing-panel h3{color:var(--white);font-size:16px;font-weight:800;text-align:center;line-height:1.3;letter-spacing:.5px}
.listing-card{margin:14px 20px 0;background:var(--white);height:200px;padding:18px 16px;text-align:left}
.listing-card .price{font-family:"Raleway",sans-serif;font-weight:800;font-size:24px;color:var(--orange)}
.listing-card .price small{font-size:13px;color:var(--muted);font-weight:600}
.listing-card h4{font-size:14px;margin:6px 0 8px;color:var(--ink)}
.listing-card p{font-size:11px;line-height:1.6;color:var(--muted)}
.listing-panel .arrow{position:absolute;top:180px;width:14px;height:24px}
.slider-dots{position:absolute;left:540px;top:570px;display:flex;gap:8px}
.slider-dots span{width:18px;height:10px;background:#2b2b2b}
.slider-dots span.on{background:var(--orange)}

/* feature cards */
.feature-row{position:absolute;left:108px;top:614px;display:flex;gap:14px}
.feature{width:316px;height:248px;position:relative}
.feature-a{background:linear-gradient(180deg,#3c4a55,#1f2a31)}
.feature-b{background:linear-gradient(160deg,#cfd7dd,#7d8e99)}
.feature-c{background:linear-gradient(160deg,#c7a985,#6d5036)}
.feature .caption{position:absolute;left:0;bottom:0;width:100%;background:rgba(0,0,0,.65);color:var(--white);font-size:11px;line-height:1.4;padding:8px 12px}
.row-arrow{position:absolute;top:724px;width:16px;height:28px}
.cta-row{position:absolute;left:0;top:880px;width:1200px;border-top:1px solid var(--line);display:flex;justify-content:center;gap:12px;padding-top:22px}
.cta-row a{background:var(--orange);color:var(--white);font-size:12px;font-weight:600;padding:6px 16px;text-decoration:none}

/* directory band */
.directory{position:absolute;left:0;top:952px;width:1200px;height:574px;background:radial-gradient(ellipse at 50% 30%,#2b2b2b 0%,var(--night) 70%);color:var(--white)}
.directory h2{position:absolute;left:0;top:60px;width:1200px;text-align:center;font-size:38px;font-weight:600}
.directory .sub{position:absolute;left:0;top:118px;width:1200px;text-align:center;font-family:"Raleway",sans-serif;font-size:21px;font-weight:600;letter-spacing:.5px}
.monitor{position:absolute;left:140px;top:212px;width:400px;height:262px}
.monitor .screen{position:absolute;left:0;top:0;width:400px;height:228px;border:10px solid #dcdcdc;border-radius:6px;background:linear-gradient(180deg,#f4f4f4,#c9ccd0)}
.monitor .stand{position:absolute;left:160px;top:228px;width:80px;height:22px;background:#bdbdbd}
.monitor .foot{position:absolute;left:120px;top:250px;width:160px;height:8px;background:#d0d0d0;border-radius:4px}
.dir-col{position:absolute;font-size:13px;line-height:1.5}
.dir-col h4{font-size:20px;font-weight:600;margin-bottom:8px}
.dir-col .opts{display:flex;gap:14px;margin:8px 0 10px;font-size:12px}
.dir-col .btn{display:inline-block;background:var(--orange);color:var(--white);padding:6px 18px;font-size:13px;font-weight:600}

/* vault */
.vault{position:absolute;left:0;top:1560px;width:1200px;height:340px;background:var(--paper)}
.vault-box{position:absolute;left:108px;top:36px;width:490px;height:272px;background:var(--white)}
.vault-box .img{position:absolute;left:0;top:0;width:190px;height:230px;background:linear-gradient(160deg,#dfe8ef,#9fb5c6)}
.vault-box h3{position:absolute;left:206px;top:14px;font-size:16px;font-weight:800;color:var(--ink)}
.vault-box p{position:absolute;font-size:11px;line-height:1.55;color:var(--muted)}
.bar{position:absolute;left:0;bottom:0;width:100%;height:42px;background:var(--orange);color:var(--white);display:flex;align-items:center;padding:0 12px;font-weight:700;font-size:14px;font-family:"Raleway",sans-serif}
.bar .nav{margin-left:auto;display:flex;gap:4px}
.bar .nav span{width:22px;height:22px;background:var(--orange-dark);display:flex;align-items:center;justify-content:center}
.affiliates{position:absolute;left:620px;top:36px;width:472px;height:272px;background:linear-gradient(160deg,#d7dde3 0%,#8c98a3 55%,#3b4550 100%)}

/* footer */
.site-footer{position:absolute;left:0;top:1920px;width:1200px;height:264px;background:var(--footer);color:#bdbdbd}
.foot-col{position:absolute;top:28px;font-size:11px;line-height:1.75}
.foot-col h4{color:var(--white);font-size:14px;font-weight:700;margin-bottom:8px;letter-spacing:.5px}
.foot-col p{width:200px}
.foot-social{display:flex;gap:8px;margin-top:4px}
.foot-social span{width:24px;height:24px;border-radius:50%;background:#8a8a8a}
.copyright{position:absolute;left:0;bottom:0;width:1200px;height:36px;background:var(--footer-bar);font-size:11px;color:#9a9a9a;line-height:36px;padding-left:110px}
</style>
</head>
<body>

<header class="site-header">
  <div class="brand"><span class="brand-square"></span><span class="brand-name">SMALLBIZ ANCHOR</span></div>
  <div class="social-top"><span></span><span></span><span></span><span></span></div>
  <div class="login-bar"><span class="field">User</span><span class="field">Password</span><span class="btn">Login</span></div>
  <nav class="main-nav">
    <a class="current" href="#">Home</a><a href="#">Coupons</a><a href="#">Mini Service</a><a href="#">Get a Quote</a><a href="#">Advertise</a><a href="#">Resource Centre</a>
  </nav>
</header>

<section class="hero" role="img" aria-label="Photo of a sunlit road winding through a tall redwood forest">
  <h1 class="hero-title"><div class="l1">IT'S A BRAND <em>NEW DAY</em></div><div class="l2">DO MORE OF <em>WHAT YOU LOVE</em></div></h1>
  <div class="hero-search"><span class="field what">What are you looking for?</span><span class="field where">Near where?</span><span class="go">GO</span></div>
  <aside class="listing-panel">
    <h3>CREATE A DIRECTORY<br>LISTING TODAY</h3>
    <div class="listing-card">
      <div class="price">$25 <small>/ YEAR</small></div>
      <h4>Standard Listing</h4>
      <p>Get your business seen by local customers. Add your logo, hours, photos and a full profile page today.</p>
    </div>
    <svg class="arrow" style="left:4px" viewBox="0 0 14 24"><path d="M11 2 3 12l8 10" fill="none" stroke="#fff" stroke-width="3"/></svg>
    <svg class="arrow" style="right:4px" viewBox="0 0 14 24"><path d="M3 2l8 10-8 10" fill="none" stroke="#fff" stroke-width="3"/></svg>
  </aside>
  <div class="slider-dots" style="top:466px"><span class="on"></span><span></span><span></span><span></span><span></span><span></span></div>
</section>

<svg class="row-arrow" style="left:80px" viewBox="0 0 16 28"><path d="M13 2 3 14l10 12" fill="none" stroke="#888" stroke-width="3"/></svg>
<div class="feature-row">
  <div class="feature feature-a" role="img" aria-label="Photo of a smartphone held in a hand">
    <div class="caption">Join Mobile Alert Club! Text your name and number to 1234 5678 to receive offers and updates.</div>
  </div>
  <div class="feature feature-b" role="img" aria-label="Photo of a businessman climbing a staircase"></div>
  <div class="feature feature-c" role="img" aria-label="Photo of a team meeting around a table"></div>
</div>
<svg class="row-arrow" style="left:1104px" viewBox="0 0 16 28"><path d="M3 2l10 12L3 26" fill="none" stroke="#888" stroke-width="3"/></svg>
<div class="cta-row"><a href="#">Sign up for Daily Deals</a><a href="#">Submit an Offer</a></div>

<section class="directory">
  <h2>Australia's Small Business Directory</h2>
  <div class="sub">FREE DIRECTORY LISTING, BUSINESS SOLUTION, BUSINESS RESOURCES</div>
  <div class="monitor">
    <div class="screen" role="img" aria-label="Screenshot of a directory website on a desktop monitor"></div>
    <div class="stand"></div><div class="foot"></div>
  </div>
  <div class="dir-col" style="left:568px;top:216px;width:300px">
    <p>Do you sell a product or service?<br>want to reach Australian small business?</p>
    <div class="opts"><span>Yes</span><span>No</span></div>
    <span class="btn">Advertise Now</span>
  </div>
  <div class="dir-col" style="left:924px;top:212px;width:220px">
    <h4>Submit an Offer</h4>
    <div class="opts"><span>Yes</span><span>No</span></div>
    <span class="btn">Submit Offer</span>
  </div>
  <div class="dir-col" style="left:568px;top:388px;width:420px">
    <h4>Join Us</h4>
    <p>We actively PROMOTE your business offer to our members!</p>
    <div class="opts"><span>Yes</span><span>No</span></div>
    <span class="btn">Join Free</span>
  </div>
</section>

<section class="vault">
  <div class="vault-box">
    <div class="img" role="img" aria-label="Photo of charts and a pen on a desk"></div>
    <h3>FROM THE VAULT</h3>
    <p style="left:206px;top:42px;width:270px">Practical tips for running a small business, from cash flow and pricing to hiring staff and marketing on a budget. Read our latest guides and get ahead.</p>
    <p style="left:12px;top:150px;width:170px"></p>
    <div class="bar"><span style="opacity:0">.</span><div class="nav">
      <span><svg width="8" height="10" viewBox="0 0 8 10"><path d="M6 1 2 5l4 4" fill="none" stroke="#fff" stroke-width="2"/></svg></span>
      <span><svg width="8" height="10" viewBox="0 0 8 10"><path d="M2 1l4 4-4 4" fill="none" stroke="#fff" stroke-width="2"/></svg></span>
    </div></div>
  </div>
  <div class="affiliates" role="img" aria-label="Photo of business partners shaking hands">
    <div class="bar">OUR AFFILIATES<div class="nav">
      <span><svg width="8" height="10" viewBox="0 0 8 10"><path d="M6 1 2 5l4 4" fill="none" stroke="#fff" stroke-width="2"/></svg></span>
      <span><svg width="8" height="10" viewBox="0 0 8 10"><path d="M2 1l4 4-4 4" fill="none" stroke="#fff" stroke-width="2"/></svg></span>
    </div></div>
  </div>
</section>

<footer class="site-footer">
  <div class="foot-col" style="left:110px">
    <h4>SITE DIRECTORY</h4>
    Search the Directory<br>Create a Directory Listing<br>Quote Finder<br>Coupons<br>Submit a Coupon<br>Advertise with Us
  </div>
  <div class="foot-col" style="left:300px">
    <h4>FORUM</h4>
    Join the Forum<br>Submit an Article or Video<br>Affiliates<br>Become an Affiliate<br>Case Studies<br>Help Guides
  </div>
  <div class="foot-col" style="left:494px">
    <h4>POPULAR CATEGORIES</h4>
    <p>Accountants, builders, cafes, cleaners, electricians, florists, gardeners, hair salons, plumbers, printers and web designers near you.</p>
  </div>
  <div class="foot-col" style="left:740px">
    <h4>ABOUT</h4>
    About Us<br>Contact Us<br>Terms and Condition<br>Privacy Policy<br>Supporting City Councils<br>Site Map
  </div>
  <div class="foot-col" style="left:950px">
    <h4>FOLLOW US</h4>
    <div class="foot-social"><span></span><span></span><span></span><span></span></div>
  </div>
  <div class="copyright">Copy right © Smallbiz Anchor. All Rights Reserved.</div>
</footer>

</body>
</html>
```